Seeking funky, innovative business cards

I am looking to refresh our current business cards to something more engaging, visual and impactful. We are a management consultancy firm, see website (www.larkstone-partners.com.au). I've included our colour scheme, sample of the slides we use and our old business cards. We would like our cards to have icons. The card should display:- Name- Title- Mobile number- Address- Email address- Website - Company logo- Our purpose statement "We create the best places on earth to work"

Contact Information for Business Card

Brennan Ulfsson
Consultant
0468 927 341
Level 3, 218 Wexley Street, Melbourne 3000
brennan@larkstone-partners.com.au
www.larkstone-partners.com.au

Purpose statement "we create the best places on earth to work"
LOGO available in google images

Font styles to use
Other font styles liked:
• Open Sans Light, Bebas Neue (open to other cool foints)

Colors
ffc214
5c5c5c
f5f5f5
fefefe

Requirements
Must have
• - Name
• - Title
• - Mobile number
• - Address
• - Email address
• - Website
• - Company logo
• - Our purpose statement "We create the best places on earth to work"
Nice to have
• - Icons
• - Colour (see our colour scheme"

```html
<!DOCTYPE html>
<html lang="en">
<head>
<meta charset="utf-8">
<title>Larkstone Partners – Business Card</title>
<link rel="stylesheet" href="https://fonts.googleapis.com/css2?family=Bebas+Neue&family=Lato:wght@300;400&display=swap">
<style>
  :root {
    --stage: #1b1b1b;
    --card: #262626;
    --accent: #ffc214;
    --ink: #f5f5f5;
    --ink-soft: #fefefe;
    --ink-muted: #bdbdbd;
  }
  * { margin: 0; padding: 0; box-sizing: border-box; }
  html, body {
    width: 1200px; height: 900px; overflow: hidden;
    background: var(--stage);
  }
  .canvas {
    position: relative; width: 1200px; height: 900px;
    display: flex; flex-direction: column; align-items: center; justify-content: center; gap: 36px;
  }
  .card {
    position: relative; width: 680px; height: 390px;
    background: linear-gradient(135deg, #242424 0%, #2b2b2b 60%, #333 100%);
    box-shadow: 0 10px 30px rgba(0,0,0,.5);
    color: var(--ink);
    font-family: "Lato", sans-serif;
  }
  /* front */
  .card-front { display: flex; align-items: center; justify-content: center; }
  .brand-lockup { display: flex; flex-direction: column; align-items: flex-end; gap: 10px; }
  .brand { display: flex; align-items: center; gap: 16px; }
  .brand-dot { width: 18px; height: 18px; border-radius: 50%; background: var(--accent); }
  .brand-name { font-weight: 300; font-size: 50px; line-height: 1; color: var(--ink-soft); letter-spacing: 0.5px; white-space: nowrap; }
  .purpose {
    font-size: 13px; font-weight: 400; letter-spacing: 2.5px; text-transform: uppercase;
    color: var(--ink-muted); white-space: nowrap;
  }
  /* back */
  .contact-block {
    position: absolute; top: 128px; left: 30px; right: 30px;
    display: flex; align-items: center; justify-content: center;
  }
  .identity { text-align: right; white-space: nowrap; }
  .person-name {
    font-family: "Bebas Neue", sans-serif; font-weight: 400; font-size: 44px; line-height: 1;
    color: var(--accent); letter-spacing: 1px;
  }
  .person-title { font-size: 18px; font-weight: 400; margin-top: 2px; }
  .divider { width: 2px; height: 92px; background: var(--accent); margin: 0 22px; flex: none; }
  .contact-list { list-style: none; font-size: 16px; line-height: 25px; white-space: nowrap; }
  .contact-list li { display: flex; align-items: center; gap: 11px; }
  .contact-list svg { width: 13px; height: 13px; flex: none; }
  .address {
    position: absolute; left: 0; right: 0; bottom: 50px;
    text-align: center; font-size: 19px; white-space: nowrap;
  }
</style>
</head>
<body>
<main class="canvas">
  <section class="card card-front">
    <div class="brand-lockup">
      <div class="brand">
        <span class="brand-dot"></span>
        <span class="brand-name">Larkstone Partners</span>
      </div>
      <p class="purpose">We create the best places on earth to work</p>
    </div>
  </section>

  <section class="card card-back">
    <div class="contact-block">
      <div class="identity">
        <h1 class="person-name">Brennan Ulfsson</h1>
        <p class="person-title">Consultant</p>
      </div>
      <div class="divider"></div>
      <ul class="contact-list">
        <li>
          <svg viewBox="0 0 16 16" aria-hidden="true"><path fill="#ffc214" d="M4 1l3 3-1.5 2a9 9 0 004.5 4.5L12 9l3 3-2 3C7 15 1 9 1 3z"/></svg>
          0468 927 341
        </li>
        <li>
          <svg viewBox="0 0 16 16" aria-hidden="true"><rect x="4" y="1" width="8" height="4" fill="#ffc214"/><rect x="1" y="6" width="14" height="6" rx="1" fill="#ffc214"/><rect x="4" y="10" width="8" height="5" fill="#ffc214" stroke="#262626"/></svg>
          + 61 3 9284 5071
        </li>
        <li>
          <svg viewBox="0 0 16 16" aria-hidden="true"><rect x="1.5" y="3.5" width="13" height="9" fill="none" stroke="#ffc214" stroke-width="1.5"/><path d="M1.5 3.5L8 9l6.5-5.5" fill="none" stroke="#ffc214" stroke-width="1.5"/></svg>
          brennan@larkstone-partners.com.au
        </li>
        <li>
          <svg viewBox="0 0 16 16" aria-hidden="true"><g fill="none" stroke="#ffc214" stroke-width="1.2"><circle cx="8" cy="8" r="6.5"/><ellipse cx="8" cy="8" rx="3" ry="6.5"/><path d="M1.5 8h13M2.5 5h11M2.5 11h11"/></g></svg>
          www.larkstone-partners.com.au
        </li>
      </ul>
    </div>
    <p class="address">Level 3, 218 Wexley Street, Melbourne 3000</p>
  </section>
</main>
</body>
</html>
```